Brightfen Business Card Redesign & Logo Update

We need to update our business cards to something more modern and fresh. Brightfen can provide the current color schemes and old design examples, but welcome creativity in helping us with this redesign. PLEASE NOTE that we no longer utilize the "tree" and/or "leaf" imagery in our branding. If able would apprecaite an update on the quality of our "words only" logo in Ai. / PNG formats too.

Target Market(s)

Investors, landowners, corporate partners, contractors

Industry/Entity Type

Environmental Restoration & Conservation

Contact Information for Business Card

Logo, persons name, title, mailing address, phone and email, website url

Font styles to use
Other font styles liked:
• Merriweather

Requirements
Nice to have
• Logo, persons name, title, mailing address, phone and email, website url, but open to ideams
Should not have
• No all back backgrounds

```html
<!DOCTYPE html>
<html lang="en">
<head>
<meta charset="utf-8">
<title>Brightfen Business Card</title>
<link rel="stylesheet" href="https://fonts.googleapis.com/css2?family=Bebas+Neue&family=Oswald:wght@500&family=Open+Sans:wght@600;700&display=swap">
<style>
  :root {
    --green: #17803e;
    --orange: #ee7f22;
    --ink: #1a1a1a;
    --paper: #ffffff;
    --backdrop: #e4e5e7;
  }
  * { box-sizing: border-box; margin: 0; padding: 0; }
  html, body { width: 1200px; height: 780px; overflow: hidden; }
  body {
    background: var(--backdrop);
    position: relative;
    font-family: "Open Sans", Arial, sans-serif;
  }
  .card {
    position: absolute;
    top: 92px;
    width: 340px;
    height: 595px;
    background: var(--paper);
    border-radius: 30px;
    box-shadow: 0 4px 0 var(--orange), 0 12px 28px rgba(0,0,0,0.18);
    overflow: hidden;
  }
  .card--front { left: 205px; }
  .card--back { left: 655px; }

  /* Front */
  .front-lockup {
    position: absolute;
    width: 540px;
    height: 190px;
    left: -100px;
    top: 202px;
    transform: rotate(-90deg);
    display: flex;
    flex-direction: column;
    justify-content: center;
    align-items: center;
  }
  .wordmark {
    font-family: "Bebas Neue", "Oswald", sans-serif;
    color: var(--green);
    line-height: 0.85;
    letter-spacing: 1px;
  }
  .front-lockup .wordmark { font-size: 140px; }
  .tagline {
    font-family: "Oswald", sans-serif;
    font-weight: 500;
    color: var(--ink);
    text-transform: uppercase;
    line-height: 1;
    letter-spacing: 0.5px;
  }
  .front-lockup .tagline { font-size: 31px; margin-top: 4px; }

  /* Back */
  .back-lockup {
    position: absolute;
    left: 34px;
    top: 58px;
  }
  .back-lockup .wordmark { font-size: 74px; }
  .back-lockup .tagline { font-size: 15.5px; margin-top: 2px; }

  .contact-block {
    position: absolute;
    left: 0;
    right: 0;
    top: 380px;
    text-align: center;
  }
  .person-name {
    font-size: 22px;
    font-weight: 700;
    line-height: 1.1;
  }
  .person-name .first { color: var(--orange); }
  .person-name .last { color: var(--green); }
  .person-title {
    font-size: 14px;
    font-weight: 600;
    color: var(--ink);
    margin-top: 2px;
  }
  .icon-row {
    position: relative;
    height: 30px;
    margin-top: 8px;
  }
  .icon-row svg.rule { position: absolute; left: 0; top: 0; }
  .contact-lines {
    margin-top: 10px;
    font-size: 14px;
    font-weight: 600;
    color: var(--ink);
    line-height: 1.55;
  }
</style>
</head>
<body>
  <section class="card card--front">
    <div class="front-lockup">
      <div class="wordmark">BRIGHTFEN</div>
      <div class="tagline">Environmental Credit Company</div>
    </div>
  </section>

  <section class="card card--back">
    <div class="back-lockup">
      <div class="wordmark">BRIGHTFEN</div>
      <div class="tagline">Environmental Credit Company</div>
    </div>

    <div class="contact-block">
      <div class="person-name"><span class="first">Marta</span> <span class="last">Kovalenko</span></div>
      <div class="person-title">Co-Founder</div>

      <div class="icon-row">
        <svg class="rule" width="340" height="30" viewBox="0 0 340 30">
          <polygon points="20,15 118,12 118,18" fill="var(--orange)"/>
          <polygon points="320,15 222,12 222,18" fill="var(--orange)"/>
          <g>
            <circle cx="140" cy="15" r="13" fill="var(--orange)"/>
            <path d="M134 9 l4 0 l1 4 l-2 1.5 a8 8 0 0 0 4 4 l1.5 -2 l4 1 l0 4 a12 12 0 0 1 -12.5 -12.5z" fill="#fff"/>
          </g>
          <g>
            <circle cx="170" cy="15" r="13" fill="var(--orange)"/>
            <rect x="162" y="10" width="16" height="11" rx="1.5" fill="none" stroke="#fff" stroke-width="1.8"/>
            <polyline points="162,11 170,17 178,11" fill="none" stroke="#fff" stroke-width="1.8"/>
          </g>
          <g>
            <circle cx="200" cy="15" r="13" fill="var(--orange)"/>
            <circle cx="200" cy="15" r="7.5" fill="none" stroke="#fff" stroke-width="1.6"/>
            <ellipse cx="200" cy="15" rx="3.2" ry="7.5" fill="none" stroke="#fff" stroke-width="1.4"/>
            <line x1="192.5" y1="15" x2="207.5" y2="15" stroke="#fff" stroke-width="1.4"/>
          </g>
        </svg>
      </div>

      <div class="contact-lines">
        <div class="phone">(555) 014-2387</div>
        <div class="email">info@brightfen.example</div>
        <div class="web">www.brightfen.example</div>
      </div>
    </div>
  </section>
</body>
</html>
```